Business card design

I already have the logo design completed and am requiring business card design and layout utilising the logo. I require a front and back design.

We are an executive recruitment company so we are looking at full colour, high finish in a reasonably conservative structure.

Reason: will be provide ai template

Target Market(s)

Senior Management 35-60 age bracket

Industry/Entity Type

Business

Requirements
Must have
• Peter Welling
• Director
• 238 Morrow Tce, Kelvin Grove QLD 4059
• Ph: 07 3628 4190 Mob: 0418527306
• peter@voltinapartners.com.au
• www.voltinapartners.com.au
Nice to have
• Ideally full colour,
Should not have
• cheap looking

```html
<!DOCTYPE html>
<html lang="en">
<head>
<meta charset="utf-8">
<title>Voltina Partners — Business Card Presentation</title>
<link rel="stylesheet" href="https://fonts.googleapis.com/css2?family=Roboto:wght@300;400&family=Roboto+Condensed:wght@300&family=EB+Garamond:wght@400&display=swap">
<style>
  :root {
    --page: #ffffff;
    --card: #e6e7e8;
    --navy: #1c3f6e;
    --ink: #4d4f52;
    --rule: #8a8c8f;
    --back-dark: #737477;
    --back-light: #8d8e91;
    --strip-dark: #5f6164;
    --strip-light: #a3a5a8;
    --divider: #c4c5c7;
    --label: #1a1a1a;
  }
  * { margin: 0; padding: 0; box-sizing: border-box; }
  html, body { width: 1200px; height: 722px; overflow: hidden; background: var(--page); }
  .sheet { position: relative; width: 1200px; height: 722px; font-family: "Roboto", Arial, sans-serif; }

  .card { position: absolute; width: 489px; height: 279px; overflow: hidden; }
  .card--front { background: var(--card); top: 23px; }
  .card--sans { left: 12px; }
  .card--serif { left: 531px; }
  .card--back { left: 531px; top: 415px; }

  .edge-strip { position: absolute; right: 0; top: 0; width: 22px; height: 100%; }
  .edge-strip__pattern { position: absolute; inset: 0 0 24% 0; background: linear-gradient(180deg, var(--strip-dark), var(--strip-light) 60%, var(--strip-dark)); }
  .edge-strip__band { position: absolute; left: 0; right: 0; bottom: 0; height: 24%; background: var(--navy); }

  .brand { position: absolute; left: 0; right: 22px; top: 42px; display: flex; align-items: center; justify-content: center; gap: 9px; }
  .brand__mark { width: 26px; height: 26px; background: var(--navy); }
  .brand__name { font-family: "Roboto", Arial, sans-serif; font-weight: 400; font-size: 20px; letter-spacing: 2px; color: var(--navy); text-transform: uppercase; white-space: nowrap; }

  .person { position: absolute; right: 268px; top: 166px; text-align: right; white-space: nowrap; }
  .person__name, .person__role { font-size: 14.5px; line-height: 19px; color: var(--navy); font-weight: 400; }
  .card--serif .person__name, .card--serif .person__role { font-family: "EB Garamond", Georgia, serif; font-size: 16px; }
  .person__contact { margin-top: 4px; font-size: 10.5px; line-height: 15px; color: var(--ink); letter-spacing: .4px; }

  .divider { position: absolute; left: 232px; top: 149px; width: 1px; height: 84px; background: var(--rule); }

  .office { position: absolute; left: 245px; top: 162px; font-size: 10.5px; line-height: 15px; color: var(--ink); letter-spacing: .4px; white-space: nowrap; }

  .back__texture { position: absolute; inset: 0; background: radial-gradient(ellipse at 30% 20%, var(--back-light), var(--back-dark) 70%); }
  .card--back .brand { right: 0; top: 124px; }
  .card--back .brand__mark { background: #fff; width: 32px; height: 32px; }
  .card--back .brand__name { color: #fff; font-size: 25px; }
  .back__web { position: absolute; left: 0; right: 0; top: 246px; text-align: center; font-size: 11px; letter-spacing: 1.5px; color: #e4e5e6; }

  .caption { position: absolute; top: 314px; font-size: 20px; color: var(--label); }
  .caption--sans { left: 12px; font-family: "Roboto", Arial, sans-serif; font-weight: 300; letter-spacing: .3px; }
  .caption--serif { left: 531px; font-family: "EB Garamond", Georgia, serif; font-size: 21px; }

  .section-rule { position: absolute; left: 0; top: 369px; width: 1200px; height: 1px; background: var(--divider); }

  .side-label { position: absolute; left: 1050px; font-family: "Roboto Condensed", Arial, sans-serif; font-weight: 300; font-size: 37px; color: var(--label); white-space: nowrap; }
  .side-label--front { top: 141px; }
  .side-label--back { top: 532px; }
</style>
</head>
<body>
<main class="sheet">

  <section class="card card--front card--sans">
    <div class="brand"><span class="brand__mark"></span><span class="brand__name">Voltina Partners</span></div>
    <div class="person">
      <p class="person__name">Peter Welling</p>
      <p class="person__role">Director</p>
      <p class="person__contact">M 0418 527 306<br>E peter@voltinapartners.com.au</p>
    </div>
    <span class="divider"></span>
    <p class="office">238 Morrow Tce, Kelvin Grove QLD 4059<br>P + 61 7 3628 4190<br>E admin@voltinapartners.com.au<br>www.voltinapartners.com.au</p>
    <div class="edge-strip">
      <div class="edge-strip__pattern" role="img" aria-label="Grey fine-line wave pattern"></div>
      <div class="edge-strip__band"></div>
    </div>
  </section>

  <section class="card card--front card--serif">
    <div class="brand"><span class="brand__mark"></span><span class="brand__name">Voltina Partners</span></div>
    <div class="person">
      <p class="person__name">Peter Welling</p>
      <p class="person__role">Director</p>
      <p class="person__contact">M 0418 527 306<br>E peter@voltinapartners.com.au</p>
    </div>
    <span class="divider"></span>
    <p class="office">238 Morrow Tce, Kelvin Grove QLD 4059<br>P + 61 7 3628 4190<br>E admin@voltinapartners.com.au<br>www.voltinapartners.com.au</p>
    <div class="edge-strip">
      <div class="edge-strip__pattern" role="img" aria-label="Grey fine-line wave pattern"></div>
      <div class="edge-strip__band"></div>
    </div>
  </section>

  <p class="caption caption--sans">“Peter Welling Director” with sans serif type font</p>
  <p class="caption caption--serif">“Peter Welling Director” with serif type font</p>
  <p class="side-label side-label--front">Front side</p>

  <div class="section-rule"></div>

  <section class="card card--back">
    <div class="back__texture" role="img" aria-label="Grey background with soft sweeping curved lines"></div>
    <div class="brand"><span class="brand__mark"></span><span class="brand__name">Voltina Partners</span></div>
    <p class="back__web">www.voltinapartners.com.au</p>
  </section>
  <p class="side-label side-label--back">Back side</p>

</main>
</body>
</html>
```